Brightfen Business Card Redesign & Logo Update

We need to update our business cards to something more modern and fresh. Brightfen can provide the current color schemes and old design examples, but welcome creativity in helping us with this redesign. PLEASE NOTE that we no longer utilize the "tree" and/or "leaf" imagery in our branding. If able would apprecaite an update on the quality of our "words only" logo in Ai. / PNG formats too.

Target Market(s)

Investors, landowners, corporate partners, contractors

Industry/Entity Type

Environmental Restoration & Conservation

Contact Information for Business Card

Logo, persons name, title, mailing address, phone and email, website url

Font styles to use
Other font styles liked:
• Merriweather

Requirements
Nice to have
• Logo, persons name, title, mailing address, phone and email, website url, but open to ideams
Should not have
• No all back backgrounds

```html
<!DOCTYPE html>
<html lang="en">
<head>
<meta charset="utf-8">
<title>Brightfen Business Card</title>
<link href="https://fonts.googleapis.com/css2?family=Oswald:wght@500;700&family=Roboto:wght@400;500&display=swap" rel="stylesheet">
<style>
  :root {
    --orange: #ee7a00;
    --green: #117a34;
    --ink: #1c1c1c;
    --paper: #ffffff;
    --backdrop: #2f2f2f;
  }
  * { margin: 0; padding: 0; box-sizing: border-box; }
  html, body { width: 1200px; height: 866px; overflow: hidden; }
  body {
    background: var(--backdrop);
    font-family: "Roboto", Arial, sans-serif;
    position: relative;
  }
  .card {
    position: absolute;
    width: 540px;
    height: 309px;
    overflow: hidden;
    box-shadow: 0 14px 30px rgba(0,0,0,.45);
  }
  .card--front { left: 45px; top: 279px; background: var(--paper); }
  .card--back {
    left: 615px; top: 279px;
    background: linear-gradient(200deg, var(--green) 0%, #2f7d26 30%, #9b7210 65%, var(--orange) 100%);
  }

  .person { position: absolute; left: 26px; top: 34px; }
  .person__name {
    font-family: "Oswald", Arial Narrow, sans-serif;
    font-weight: 700;
    font-size: 27px;
    letter-spacing: .5px;
    line-height: 1;
    font-style: italic;
    text-transform: uppercase;
  }
  .person__first { color: var(--orange); }
  .person__last { color: var(--green); }
  .person__title {
    margin-top: 5px;
    font-size: 12.5px;
    font-weight: 500;
    letter-spacing: .6px;
    color: var(--ink);
    text-transform: uppercase;
  }

  .divider {
    position: absolute;
    left: 26px; right: 36px; top: 112px;
    height: 1px;
    background: var(--green);
  }

  .contact { position: absolute; left: 26px; top: 124px; list-style: none; }
  .contact li {
    display: flex; align-items: center; gap: 7px;
    font-size: 13px; color: var(--ink); letter-spacing: .4px;
    line-height: 20px;
  }
  .contact svg { width: 13px; height: 13px; flex: none; }

  .brand {
    position: absolute; right: 34px; top: 30px;
    text-align: center;
  }
  .brand__name {
    font-family: "Oswald", Arial Narrow, sans-serif;
    font-weight: 700;
    font-size: 46px;
    line-height: 1;
    letter-spacing: 1px;
    color: var(--green);
    text-transform: uppercase;
  }
  .brand__tagline {
    margin-top: 4px;
    font-family: "Oswald", Arial Narrow, sans-serif;
    font-weight: 500;
    font-size: 12.5px;
    letter-spacing: .8px;
    color: var(--ink);
    text-transform: uppercase;
  }

  .address {
    position: absolute; right: 36px; top: 206px;
    text-align: right;
    font-size: 13.5px; line-height: 19px;
    color: var(--ink); letter-spacing: .4px;
  }

  .footer-band { position: absolute; left: 0; bottom: 0; width: 540px; height: 48px; }
  .website {
    position: absolute; right: 36px; bottom: 8px;
    font-size: 13.5px; letter-spacing: .6px;
    color: var(--paper);
  }

  .back-brand {
    position: absolute; left: 0; right: 0; top: 110px;
    text-align: center;
  }
  .back-brand .brand__name { color: var(--paper); font-size: 62px; }
  .back-brand .brand__tagline { color: var(--paper); font-size: 16px; letter-spacing: 1.2px; }
</style>
</head>
<body>

  <section class="card card--front" aria-label="Business card front">
    <div class="person">
      <div class="person__name"><span class="person__first">Marcus</span> <span class="person__last">Hale</span></div>
      <div class="person__title">Managing Director</div>
    </div>

    <div class="divider"></div>

    <ul class="contact">
      <li>
        <svg viewBox="0 0 16 16" aria-hidden="true"><path fill="#ee7a00" d="M3.6 1.5l2.2 2.6-1.3 1.6c.9 2 2.4 3.5 4.4 4.4l1.6-1.3 2.6 2.2-1.2 2.3C6.8 13.1 2.9 9.2 1.2 2.7z"/></svg>
        044-987 210 655
      </li>
      <li>
        <svg viewBox="0 0 16 16" aria-hidden="true"><rect x="1" y="3" width="14" height="10" fill="#ee7a00"/><path d="M1 3l7 6 7-6" fill="none" stroke="#fff" stroke-width="1.3"/></svg>
        hello@brightfen.org
      </li>
    </ul>

    <div class="brand">
      <div class="brand__name">Brightfen</div>
      <div class="brand__tagline">Environmental Credit Company</div>
    </div>

    <address class="address" style="font-style:normal">
      421, Address line goes here<br>
      45452,Country Name
    </address>

    <svg class="footer-band" viewBox="0 0 540 48" preserveAspectRatio="none" aria-hidden="true">
      <path fill="#117a34" d="M0 28 L185 28 L185 32 L0 32 Z"/>
      <path fill="#ee7a00" d="M0 36 L190 36 C215 36 222 22 250 22 L540 22 L540 48 L0 48 Z"/>
    </svg>
    <div class="website">www.brightfen.org</div>
  </section>

  <section class="card card--back" aria-label="Business card back">
    <div class="back-brand">
      <div class="brand__name">Brightfen</div>
      <div class="brand__tagline">Environmental Credit Company</div>
    </div>
  </section>

</body>
</html>
```